Printer Cartridges Supplier Namecard

Attached is my company logo and the design of my current namecard. I would like to have a more special look for it. Can have a little cuteness too rather than those normal standard feel. I'm a supplier mainly dealing with original and compatible printer toner cartridges, some other products like paper supplies as well.

Target Market(s)

Companies, businesses, corporates

Industry/Entity Type

It Company

Contact Information for Business Card

Logo, name, contact, address, supplies and maybe a slogan

Colors
85cae6
33a6d7
3176b5
0255a3
0792cd
85abd2

Requirements
Must have
• Logo, name, contact and address basic details.
• Must include some pictures, not just rearrange what I'm currently having.
Nice to have
• Be creative and bold, a diiferent traditional feel.

```html
<!DOCTYPE html>
<html lang="en">
<head>
<meta charset="utf-8">
<title>Tonerden Business Card</title>
<link rel="stylesheet" href="https://fonts.googleapis.com/css2?family=Lato:wght@400;700&family=Arimo:wght@400&display=swap">
<style>
  :root {
    --page-bg: #ececec;
    --card-grey: #58595b;
    --band-white: #ffffff;
    --accent-blue: #5ab4e5;
    --text-light: #ffffff;
    --text-dark: #2e2e2e;
    --logo-grey: #5d5e60;
  }
  html, body {
    margin: 0;
    padding: 0;
    width: 1200px;
    height: 900px;
    overflow: hidden;
    background: var(--page-bg);
  }
  .card {
    position: absolute;
    left: 120px;
    top: 152px;
    width: 960px;
    height: 596px;
    border-radius: 24px;
    background: var(--card-grey);
    overflow: hidden;
    font-family: "Lato", sans-serif;
    color: var(--text-light);
    box-shadow: 0 10px 30px rgba(0,0,0,0.15);
  }
  .line {
    position: absolute;
    white-space: nowrap;
    line-height: 36px;
    font-size: 27px;
  }
  .right { text-align: right; }
  .contact-icon {
    position: absolute;
    right: 63px;
    width: 18px;
    height: 18px;
  }
  .band {
    position: absolute;
    left: 0;
    top: 224px;
    width: 960px;
    height: 148px;
    background: var(--band-white);
  }
  .logo-box {
    position: absolute;
    left: 15px;
    top: 183px;
    width: 273px;
    height: 229px;
    border-radius: 16px;
    background: var(--band-white);
  }
  .logo-dot {
    position: absolute;
    left: 64px;
    top: 241px;
    width: 100px;
    height: 100px;
    border-radius: 50%;
    background: var(--accent-blue);
  }
  .brand-name {
    position: absolute;
    left: 190px;
    top: 240px;
    font-size: 84px;
    line-height: 100px;
    font-weight: 400;
    color: var(--logo-grey);
    letter-spacing: -1px;
  }
  .brand-tagline {
    position: absolute;
    left: 196px;
    top: 333px;
    font-size: 16px;
    line-height: 20px;
    font-weight: 700;
    color: var(--logo-grey);
    white-space: nowrap;
  }
  .person-name {
    right: 62px;
    top: 259px;
    font-family: "Arimo", sans-serif;
    font-size: 41px;
    line-height: 46px;
    color: var(--accent-blue);
  }
  .person-title {
    right: 62px;
    top: 298px;
    color: var(--text-dark);
  }
  .service { right: 84px; font-size: 28px; }
  .service-dot {
    position: absolute;
    right: 65px;
    width: 9px;
    height: 9px;
    border-radius: 50%;
    background: var(--accent-blue);
  }
  .website {
    left: 52px;
    top: 524px;
    color: var(--accent-blue);
  }
</style>
</head>
<body>
  <div class="card">
    <div class="line right" style="right:93px; top:45px;">8456 1307</div>
    <svg class="contact-icon" style="top:54px;" viewBox="0 0 18 18" aria-hidden="true">
      <rect x="4" y="1" width="10" height="16" rx="2" fill="none" stroke="var(--accent-blue)" stroke-width="2"/>
      <rect x="7" y="13" width="4" height="1.6" fill="var(--accent-blue)"/>
    </svg>

    <div class="line right" style="right:93px; top:82px;">mira@tonerden.sg</div>
    <svg class="contact-icon" style="top:92px;" viewBox="0 0 18 18" aria-hidden="true">
      <rect x="1" y="3" width="16" height="12" fill="var(--accent-blue)"/>
      <path d="M1 3 L9 10 L17 3" fill="none" stroke="var(--card-grey)" stroke-width="1.5"/>
    </svg>

    <div class="line right" style="right:62px; top:131px;">47A Harbourview Lane</div>
    <div class="line right" style="right:62px; top:167px;">#05-112, Singapore 530417</div>

    <div class="band"></div>
    <div class="logo-box"></div>
    <div class="logo-dot"></div>
    <div class="brand-name">tonerden</div>
    <div class="brand-tagline">Compatible printer ink and toner solutions</div>

    <div class="line right person-name">Mira Tan</div>
    <div class="line right person-title">Sales Executive</div>

    <div class="line right service" style="top:421px;">Printer Ink &amp; Toner Cartridges</div>
    <div class="service-dot" style="top:435px;"></div>
    <div class="line right service" style="top:455px;">Original Printer Cartridges</div>
    <div class="service-dot" style="top:469px;"></div>
    <div class="line right service" style="top:490px;">Paper Products</div>
    <div class="service-dot" style="top:504px;"></div>
    <div class="line right service" style="top:526px;">Printer Maintainence &amp; Repair</div>
    <div class="service-dot" style="top:540px;"></div>

    <div class="line website">www.tonerden.sg</div>
  </div>
</body>
</html>
```